Flyer Promoting Dental Benefit Program

I want to promote a dental benefit program to my patients that do not have dental insurance. This flyer would be posted in our waiting room and where people make payments. The goal would be to get those interested to request more information and enroll in the program. I have a card that will be issued that has a logo. Theflyer and card should feel congruent. I've uploaded a file with a copy of that card.
The plan costs $290/person. It includes 2 cleanings, exams, and x-rays. It also includes a 20% discount off of our standard fees. The plan or membership lasts for one year. It is only available to those without insurance. It is also important to let people know that this is not insurance (some kind of a disclaimer).
Updates
This plan is only available to patients at my office. The contact information is: Harborview Dental, 2718 West 4600 North Suite 209, Salt Lake City, Utah 84157. (801) 563-9071. info@harborviewdental-example.com. It is not necessary to include contact information as this flyer will be used as in-office promotion.
Target Market(s)
Those without dental insurance, but have resources to afford dental care.
Industry/Entity Type
Insurance
Look and feel
Each slider illustrates characteristics of the customer's brand and the style your logo design should communicate.

```html
<!DOCTYPE html>
<html lang="en">
<head>
<meta charset="utf-8">
<title>Dental Benefit Program Flyer</title>
<link rel="stylesheet" href="https://fonts.googleapis.com/css2?family=Roboto+Condensed:wght@700&family=Open+Sans:wght@400;600&family=Indie+Flower&family=PT+Serif:ital,wght@1,700&display=swap">
<style>
  :root {
    --green: #3d9b35;
    --green-light: #8fd07c;
    --ink: #222;
    --grey: #444;
    --soft-grey: #666;
    --badge: #231f1f;
    --page-bg: #e6e6e3;
    --paper: #ffffff;
  }
  * { margin: 0; padding: 0; box-sizing: border-box; }
  html, body { width: 931px; height: 1200px; overflow: hidden; background: var(--page-bg); }
  .flyer {
    position: absolute; left: 53px; top: 20px;
    width: 824px; height: 1160px;
    background: var(--paper);
    overflow: hidden;
    box-shadow: 0 2px 10px rgba(0,0,0,.18);
  }
  .headline {
    position: absolute; left: 66px; top: 36px; width: 240px;
    font: 700 41px/60px "Roboto Condensed", sans-serif;
    color: var(--green);
  }
  .headline span { display: block; white-space: nowrap; }
  .photo {
    position: absolute; border-radius: 50%;
    border: 12px solid var(--green);
    box-shadow: inset 0 0 0 10px var(--green-light);
  }
  .photo-top {
    left: 326px; top: -20px; width: 462px; height: 462px;
    background: radial-gradient(circle at 45% 45%, #f1d8c4 0%, #d8b08e 40%, #8a6a3e 75%, #5e7a34 100%);
  }
  .photo-bottom {
    left: 448px; top: 391px; width: 364px; height: 364px;
    background: radial-gradient(circle at 50% 50%, #e8c8ae 0%, #c99a82 40%, #9ab07a 75%, #6f8f52 100%);
  }
  .includes-lead {
    position: absolute; left: 66px; top: 545px;
    font: 400 50px/1 "Indie Flower", cursive;
    color: var(--soft-grey);
  }
  .includes-list {
    position: absolute; left: 66px; top: 614px;
    font: 600 25px/1.2 "Open Sans", sans-serif;
    color: var(--grey);
  }
  .program-name {
    position: absolute; left: 61px; top: 760px;
    display: flex; align-items: center; gap: 18px;
  }
  .program-name .dot {
    width: 106px; height: 106px; border-radius: 50%; background: var(--green);
  }
  .program-name span {
    font: 700 38px/1 "Roboto Condensed", sans-serif;
    color: var(--grey); letter-spacing: .5px;
  }
  .terms {
    position: absolute; left: 66px; top: 906px; width: 368px;
    font: 400 18.5px/27px "Open Sans", sans-serif;
    color: var(--ink); text-align: justify;
  }
  .badge-shadow {
    position: absolute; left: 522px; top: 1058px; width: 200px; height: 16px;
    border-radius: 50%; background: radial-gradient(ellipse, rgba(0,0,0,.45), rgba(0,0,0,0) 70%);
  }
  .badge {
    position: absolute; left: 515px; top: 851px; width: 214px; height: 214px;
    border-radius: 50%; background: var(--badge);
    border: 10px solid var(--green);
    box-shadow: inset 0 0 0 5px var(--green-light);
    display: flex; flex-direction: column; align-items: center; justify-content: center;
    color: #fff; text-align: center;
  }
  .badge .big { font: 700 36px/1.02 "Roboto Condensed", sans-serif; }
  .badge .small { font: italic 700 25px/1.02 "PT Serif", serif; }
  .badge .big + .small { margin-top: 4px; }
  .swoosh { position: absolute; left: 0; top: 0; width: 824px; height: 1160px; }
  .contact {
    position: absolute; left: 0; top: 1108px; width: 824px;
    font: 400 13px/20px "Open Sans", sans-serif;
    color: #fff; text-align: center;
  }
  .contact b { font-weight: 600; }
</style>
</head>
<body>
  <main class="flyer">
    <div class="photo photo-top" role="img" aria-label="Photo of a smiling young couple lying on grass"></div>
    <div class="photo photo-bottom" role="img" aria-label="Photo of a smiling couple outdoors, one on the other's back"></div>

    <h1 class="headline">
      <span>Dental</span>
      <span>benefit</span>
      <span>program to</span>
      <span>my patients</span>
      <span>that do not</span>
      <span>have dental</span>
      <span>insurance</span>
    </h1>

    <p class="includes-lead">it include s</p>
    <p class="includes-list">2 cleanings, Exams, &amp; X-rays</p>

    <div class="program-name">
      <div class="dot"></div>
      <span>SMILE SAVINGS PLAN</span>
    </div>

    <p class="terms">The plan or membership lasts for one year. It is only available to those without insurance. It is also important to let people know that this is not insurance (some kind of a disclaimer).</p>

    <div class="badge-shadow"></div>
    <div class="badge">
      <span class="big">20%</span>
      <span class="big">discount</span>
      <span class="small">off our</span>
      <span class="small">standard</span>
      <span class="small">fees.</span>
    </div>

    <svg class="swoosh" viewBox="0 0 824 1160" aria-hidden="true">
      <path d="M0 1136 Q 250 1058 510 1074 Q 260 1070 0 1150 Z" fill="#2b2b2b"/>
      <path d="M0 1160 L0 1152 Q 290 1070 520 1080 Q 700 1090 824 1132 L824 1160 Z" fill="var(--green)"/>
    </svg>

    <div class="contact">
      <p>Harborview Dental, 2718 West 4600 North Suite 209, Salt Lake City, Utah 84157.</p>
      <p><b>Tel:</b> (801) 563-9071 &nbsp;<b>Email:</b> info@harborviewdental-example.com.</p>
    </div>
  </main>
</body>
</html>
```